Design a New Business Card for Our Company

We are looking for fresh, unique, and a modern business card that reflects our roots as digital marketing agency focused on SEM.

Industry/Entity Type

Marketing

Contact Information for Business Card

looking for very unique out of the box designs. clean and modern that compliments our logo

Requirements
Must have
• colors should match our logo
• Front should have name, address, email, and phone/fax of the person, phone/fax are the same number
• back should have our url

```html
<!DOCTYPE html>
<html lang="en">
<head>
<meta charset="utf-8">
<title>Tidewell Solutions – Business Card</title>
<link rel="stylesheet" href="https://fonts.googleapis.com/css2?family=Source+Sans+3:wght@400;600;700&display=swap">
<style>
  :root {
    --backdrop: #2e2e2e;
    --card-grey: #b1b1b1;
    --stripe-grey: #a9a9a9;
    --brand-blue: #5a95d0;
    --paper: #ffffff;
    --icon-grey: #c9c9c9;
    --faint-grey: #ededed;
  }
  * { box-sizing: border-box; margin: 0; padding: 0; }
  html, body {
    width: 1200px; height: 900px; overflow: hidden;
    background: var(--backdrop);
    font-family: "Source Sans 3", "Myriad Pro", Arial, sans-serif;
  }
  .stage { position: relative; width: 1200px; height: 900px; }
  .card {
    position: absolute; left: 290px; width: 620px; height: 354px;
    overflow: hidden; box-shadow: 0 12px 30px rgba(0,0,0,.45);
  }
  .card--back { top: 70px; background: var(--card-grey); }
  .card--front { top: 476px; background: var(--paper); }

  .brand__name { font-weight: 700; line-height: 1; white-space: nowrap; letter-spacing: -0.5px; }

  /* back */
  .back__circle {
    position: absolute; left: 60px; top: 62px;
    width: 230px; height: 230px; border-radius: 50%;
    background: var(--paper);
  }
  .card--back .brand__name {
    position: absolute; right: 36px; bottom: 92px;
    color: var(--paper); font-size: 34px;
  }
  .back__url {
    position: absolute; right: 36px; bottom: 62px;
    color: var(--paper); font-size: 17px; white-space: nowrap;
  }

  /* front */
  .front__panel { position: absolute; inset: 0; }
  .front__circle {
    position: absolute; left: 420px; top: 110px;
    width: 170px; height: 170px; border-radius: 50%;
    background: var(--faint-grey);
  }
  .card--front .brand__name {
    position: absolute; left: 372px; top: 32px;
    color: var(--brand-blue); font-size: 26px;
  }

  .person { position: absolute; right: 306px; top: 34px; text-align: right; color: var(--paper); }
  .person__name { font-weight: 700; font-size: 21px; line-height: 1.1; white-space: nowrap; }
  .person__title { font-size: 14px; }

  .contact { position: absolute; color: var(--paper); font-size: 15.5px; text-align: right; line-height: 1.25; white-space: nowrap; }
  .contact--address { right: 282px; top: 150px; }
  .contact-line { position: absolute; display: flex; align-items: center; gap: 8px; color: var(--paper); font-size: 15.5px; white-space: nowrap; }
  .contact-line .icon {
    width: 17px; height: 17px; border-radius: 3px; background: var(--icon-grey);
    display: flex; align-items: center; justify-content: center;
  }
  .contact-line .icon svg { width: 11px; height: 11px; }
</style>
</head>
<body>
<main class="stage">

  <section class="card card--back" aria-label="Card back">
    <span class="back__circle" aria-hidden="true"></span>
    <p class="brand__name">Tidewell Solutions</p>
    <p class="back__url">www.tidewellsolutions.com</p>
  </section>

  <section class="card card--front" aria-label="Card front">
    <svg class="front__panel" viewBox="0 0 620 354" width="620" height="354" aria-hidden="true">
      <polygon points="0,0 346,0 388,354 0,354" fill="var(--stripe-grey)"/>
      <polygon points="0,0 334,0 376,354 0,354" fill="var(--brand-blue)"/>
      <polygon points="336,20 356,36 340,52" fill="var(--brand-blue)"/>
    </svg>

    <span class="front__circle" aria-hidden="true"></span>
    <p class="brand__name">Tidewell Solutions</p>

    <div class="person">
      <p class="person__name">Dana Whitfield</p>
      <p class="person__title">Owner</p>
    </div>

    <p class="contact contact--address">48 Harbor Lane, Suite 200,<br>Riverton, OR 97001</p>

    <p class="contact-line" style="right:272px; top:208px;">555.010.2030
      <span class="icon"><svg viewBox="0 0 12 12"><path d="M2 1h3l1 3-2 1a7 7 0 0 0 3 3l1-2 3 1v3c-6 0-9-3-9-9z" fill="#fff"/></svg></span>
    </p>
    <p class="contact-line" style="right:270px; top:230px;">555.010.2030
      <span class="icon"><svg viewBox="0 0 12 12"><rect x="1" y="5" width="10" height="6" rx="1" fill="#fff"/><rect x="3" y="1" width="6" height="4" fill="#fff"/></svg></span>
    </p>
    <p class="contact-line" style="right:267px; top:252px;">hello@tidewellsolutions.com
      <span class="icon"><svg viewBox="0 0 12 12"><rect x="1" y="3" width="10" height="7" fill="#fff"/><path d="M1 3l5 4 5-4" stroke="#c9c9c9" fill="none"/></svg></span>
    </p>
    <p class="contact-line" style="right:264px; top:274px;">www.tidewellsolutions.com
      <span class="icon"><svg viewBox="0 0 12 12"><circle cx="6" cy="6" r="4.5" stroke="#fff" stroke-width="1.4" fill="none"/><path d="M1.5 6h9M6 1.5v9" stroke="#fff" stroke-width="1"/></svg></span>
    </p>
  </section>

</main>
</body>
</html>
```